TALMORK

The business want a professional looking business card. We have a scetch we will add but want the extra upgrade, and would like more suggestions for variations of our business cards.

```html
<!DOCTYPE html>
<html lang="en">
<head>
<meta charset="utf-8">
<title>TALMORK – Business Card</title>
<link rel="stylesheet" href="https://fonts.googleapis.com/css2?family=Montserrat:wght@400;500;700&family=Cinzel:wght@500;700&display=swap">
<style>
  :root {
    --backdrop: #141414;
    --card: #1f1f1f;
    --card-edge: #262626;
    --gold: #b98f3a;
    --gold-light: #d4ac55;
    --text-light: #eeeeee;
    --mark-dark: #191919;
    --mark-mid: #3a3a3a;
    --pattern-light: #5a5a5a;
  }
  * { box-sizing: border-box; margin: 0; padding: 0; }
  html, body {
    width: 1200px; height: 1059px; overflow: hidden;
    background: var(--backdrop);
  }
  .canvas { position: relative; width: 1200px; height: 1059px; }

  .card {
    position: absolute;
    width: 689px; height: 392px;
    background: var(--card);
    border-radius: 16px;
    overflow: hidden;
    box-shadow: 0 10px 24px rgba(0,0,0,.55);
  }
  .card--front { left: 257px; top: 89px; }
  .card--back  { left: 254px; top: 546px; width: 693px; height: 394px; }

  /* front */
  .brand {
    position: absolute; left: 37px; top: 48px; width: 318px;
    text-align: center;
  }
  .brand__name {
    font-family: "Montserrat", sans-serif; font-weight: 500;
    font-size: 44px; letter-spacing: 12px; line-height: 1;
    color: var(--gold);
    padding-left: 12px;
  }
  .brand__since {
    margin-top: 14px;
    font-family: "Cinzel", serif; font-weight: 700;
    font-size: 13px; letter-spacing: 8px;
    color: var(--gold);
    padding-left: 8px;
  }
  .accent-bar {
    position: absolute; left: 0; top: 176px;
    width: 21px; height: 43px;
    background: var(--gold);
  }
  .person { position: absolute; left: 42px; top: 172px; }
  .person__name {
    font-family: "Montserrat", sans-serif; font-weight: 700;
    font-size: 23px; color: var(--gold-light); line-height: 1.1;
  }
  .person__role {
    font-family: "Montserrat", sans-serif; font-weight: 400;
    font-size: 18px; color: var(--text-light); margin-top: 4px;
  }
  .contacts {
    position: absolute; left: 42px; top: 257px; list-style: none;
  }
  .contacts li {
    display: flex; align-items: center; gap: 12px;
    height: 33.5px;
    font-family: "Montserrat", sans-serif; font-weight: 400;
    font-size: 19px; color: var(--text-light); letter-spacing: .3px;
  }
  .contacts svg { width: 15px; height: 15px; flex: none; }

  .emblem-area {
    position: absolute; left: 371px; top: 43px;
    width: 305px; height: 306px;
    border-radius: 50%;
    background: radial-gradient(circle at 55% 40%, var(--mark-mid) 0%, #262626 45%, var(--card) 72%);
  }

  /* back */
  .pattern-area {
    position: absolute; inset: 0;
    background: linear-gradient(100deg, var(--mark-dark) 0%, #232323 45%, var(--pattern-light) 100%);
    opacity: .55;
  }
  .back-brand {
    position: absolute; left: 464px; top: 150px; width: 164px;
    height: 160px;
    display: flex; flex-direction: column; align-items: center; justify-content: flex-end;
    background: var(--card);
    border-radius: 12px;
    padding-bottom: 10px;
  }
  .back-brand__dot {
    width: 44px; height: 44px; border-radius: 50%;
    background: var(--gold);
    margin-bottom: 22px;
  }
  .back-brand__name {
    font-family: "Montserrat", sans-serif; font-weight: 500;
    font-size: 20px; letter-spacing: 5px; line-height: 1;
    color: var(--gold); padding-left: 5px;
  }
  .back-brand__since {
    margin-top: 7px;
    font-family: "Cinzel", serif; font-weight: 700;
    font-size: 7px; letter-spacing: 4px; color: var(--gold);
    padding-left: 4px;
  }
</style>
</head>
<body>
<main class="canvas">

  <section class="card card--front" aria-label="Business card front">
    <div class="brand">
      <div class="brand__name">TALMORK</div>
      <div class="brand__since">SINCE 2026</div>
    </div>

    <span class="accent-bar"></span>
    <div class="person">
      <div class="person__name">Halvard Brekke</div>
      <div class="person__role">CEO &amp; Founder</div>
    </div>

    <ul class="contacts">
      <li>
        <svg viewBox="0 0 24 24" aria-hidden="true"><path fill="var(--gold)" d="M6.6 10.8a15 15 0 0 0 6.6 6.6l2.2-2.2a1 1 0 0 1 1-.25 11.4 11.4 0 0 0 3.6.57 1 1 0 0 1 1 1V20a1 1 0 0 1-1 1A17 17 0 0 1 3 4a1 1 0 0 1 1-1h3.5a1 1 0 0 1 1 1c0 1.25.2 2.45.57 3.57a1 1 0 0 1-.25 1z"/></svg>
        004795512064
      </li>
      <li>
        <svg viewBox="0 0 24 24" aria-hidden="true"><path fill="var(--gold)" d="M2 9l10-6 10 6v11H2zm2 1.2V18h16v-7.8l-8 5z"/></svg>
        talmork.llc@mailhub.com
      </li>
      <li>
        <svg viewBox="0 0 24 24" aria-hidden="true"><circle cx="12" cy="12" r="9.5" fill="none" stroke="var(--gold)" stroke-width="2"/><path fill="var(--gold)" d="M7 6c2 1 3 3 2 5s1 3 1 5l-2 3c-3-2-5-5-4.5-9zM14 4c2 2 1 4 3 5s3 1 3 3l-3 1-2-2-2 1z"/></svg>
        www.talmork.llc
      </li>
    </ul>

    <div class="emblem-area" role="img" aria-label="Large embossed brand emblem in dark grey"></div>
  </section>

  <section class="card card--back" aria-label="Business card back">
    <div class="pattern-area" role="img" aria-label="Repeating emblem pattern fading from black to grey"></div>
    <div class="back-brand">
      <span class="back-brand__dot"></span>
      <div class="back-brand__name">TALMORK</div>
      <div class="back-brand__since">SINCE 2026</div>
    </div>
  </section>

</main>
</body>
</html>
```